Human Resource Consulting practice needs a business card design

We need a business card design (double sided colour) for our Human Resource (HR) consulting practice in regional New South Wales, australia. Our business name is Staff Compass. We support small and medium business across the Mid North Coast of New South Wales by providing them with outsourced HR support, services and products to help them achieve compliance with workplace legislation and across all areas of the employment lifecycle from recruitment to termination and everything in between. Our corporate colours are hot pink and black. The final design should communicate professionalism, trust, people focus.
I have attached the current (old) business card for your reference.

Target Market(s)

Business owners and high level managers

Industry/Entity Type

Business

Contact Information for Business Card

Name
Title
Phone no
Mobile no
Address
PO Box
email address
website

Colors
e34197

Requirements
Must have
• Tempate for changing business card personal details including Name, position title, mobile number, email address.
• Keep current logo and colours as per attached
• Logo must be presented in 2 colours or black only not white
Nice to have
• One side logo and graphic only other side logo and personal details
Should not have
• Should not be the same as the current version (attached) but a modern interpretation.
• Does not need a busy reverse side with our list of services as per current version. I feel this is too busy.
• No photos

```html
<!DOCTYPE html>
<html lang="en">
<head>
<meta charset="utf-8">
<title>Staff Compass – Business Card</title>
<link rel="stylesheet" href="https://fonts.googleapis.com/css2?family=Michroma&display=swap">
<style>
  :root {
    --hot-pink: #e3218f;
    --charcoal: #333333;
    --ink: #3a3a3a;
    --soft-grey: #b5b5b5;
    --card-white: #ffffff;
    --backdrop: #e9e9ec;
  }
  * { box-sizing: border-box; margin: 0; padding: 0; }
  html, body {
    width: 1200px; height: 900px; overflow: hidden;
    background: var(--backdrop);
    font-family: "Michroma", sans-serif;
  }
  .sheet {
    width: 1200px; height: 900px;
    display: flex; flex-direction: column;
    align-items: center; justify-content: center; gap: 40px;
  }
  .card {
    position: relative;
    width: 700px; height: 400px;
    background: radial-gradient(ellipse at 50% 40%, #ffffff 55%, #f1f1f1 100%);
    border-radius: 34px;
    overflow: hidden;
    box-shadow: 0 6px 20px rgba(0,0,0,0.12);
  }
  .card__rule {
    position: absolute; left: 0; right: 0; height: 10px;
    background: var(--charcoal);
  }
  .card__rule--top { top: 0; }
  .card__rule--bottom { bottom: 0; }
  .card__rule::after {
    content: ""; position: absolute; left: 0; right: 0; height: 3px;
    background: var(--hot-pink);
  }
  .card__rule--top::after { top: 14px; }
  .card__rule--bottom::after { bottom: 14px; }
  .wordmark {
    display: flex; align-items: center; gap: 12px;
    color: var(--hot-pink);
    font-weight: 400;
    letter-spacing: 0.02em;
    white-space: nowrap;
  }
  .wordmark__dot {
    width: 14px; height: 14px; border-radius: 50%;
    background: var(--soft-grey);
  }
  .card--back .wordmark {
    position: absolute; left: 50%; top: 50%;
    transform: translate(-50%, -50%);
    font-size: 40px;
  }
  .card--front .wordmark {
    position: absolute; left: 50%; top: 92px;
    transform: translateX(-50%);
    font-size: 34px;
  }
  .details {
    position: absolute; left: 60px; right: 60px; top: 216px;
    display: flex; justify-content: center;
  }
  .details__person {
    text-align: right;
    padding-right: 22px;
    font-size: 12px; line-height: 1.75;
    color: var(--ink);
    font-variant: small-caps;
  }
  .details__name { color: var(--hot-pink); font-size: 14px; }
  .details__divider {
    width: 1px; background: linear-gradient(transparent, #9a9a9a 15%, #9a9a9a 85%, transparent);
  }
  .details__contacts {
    list-style: none;
    padding-left: 16px;
    font-size: 11.5px; line-height: 1.85;
    color: var(--ink);
  }
  .contact { display: flex; align-items: center; gap: 8px; }
  .contact__icon { width: 13px; height: 13px; flex: none; }
</style>
</head>
<body>
<main class="sheet">

  <section class="card card--back" aria-label="Card back">
    <div class="wordmark"><span class="wordmark__dot"></span>Staff Compass</div>
  </section>

  <section class="card card--front" aria-label="Card front">
    <div class="card__rule card__rule--top"></div>
    <div class="card__rule card__rule--bottom"></div>

    <div class="wordmark"><span class="wordmark__dot"></span>Staff Compass</div>

    <div class="details">
      <div class="details__person">
        <p class="details__name">Daniel Hartley</p>
        <p>Principal Consultant</p>
        <p>Level 2, 14 Horton St,</p>
        <p>Port Macquarie NSW 2444</p>
      </div>
      <div class="details__divider"></div>
      <ul class="details__contacts">
        <li class="contact">
          <svg class="contact__icon" viewBox="0 0 14 14"><circle cx="7" cy="7" r="7" fill="var(--hot-pink)"/><path d="M4.5 3.5 L6 3.5 L6.5 5.3 L5.6 6 Q6.4 7.8 8 8.4 L8.7 7.5 L10.5 8 L10.5 9.5 Q7.5 10.5 5 8 Q3.5 6 4.5 3.5Z" fill="#fff"/></svg>
          <span>02 6584 3170</span>
        </li>
        <li class="contact">
          <svg class="contact__icon" viewBox="0 0 14 14"><circle cx="7" cy="7" r="7" fill="var(--hot-pink)"/><rect x="5" y="3" width="4" height="8" rx="0.8" fill="#fff"/></svg>
          <span>0412 558 904</span>
        </li>
        <li class="contact">
          <svg class="contact__icon" viewBox="0 0 14 14"><circle cx="7" cy="7" r="7" fill="var(--hot-pink)"/><rect x="4" y="5" width="6" height="5" fill="#fff"/><path d="M4 5 L7 3 L10 5Z" fill="#fff"/></svg>
          <span>PO Box 812</span>
        </li>
        <li class="contact">
          <svg class="contact__icon" viewBox="0 0 14 14"><circle cx="7" cy="7" r="7" fill="var(--hot-pink)"/><rect x="3.5" y="4.5" width="7" height="5" fill="#fff"/><path d="M3.5 4.5 L7 7.3 L10.5 4.5" fill="none" stroke="var(--hot-pink)" stroke-width="0.8"/></svg>
          <span>daniel@staffcompass.com.au</span>
        </li>
        <li class="contact">
          <svg class="contact__icon" viewBox="0 0 14 14"><circle cx="7" cy="7" r="7" fill="var(--hot-pink)"/><circle cx="7" cy="7" r="3.5" fill="none" stroke="#fff" stroke-width="1"/><path d="M3.5 7 H10.5 M7 3.5 V10.5" stroke="#fff" stroke-width="0.8"/></svg>
          <span>www.staffcompass.com.au</span>
        </li>
      </ul>
    </div>
  </section>

</main>
</body>
</html>
```